Kor'v Meridell Travel

We need a sleek, professional, inviting card to elicit global travel for the experienced and professional traveler. Royal blue, black and silver. (perhaps the wording could be silver with black shadow?-get creative) Maybe a watermark on the front and the full raised logo on the back.
We want a stylish and modern card, but professional.

```html
<!DOCTYPE html>
<html lang="en">
<head>
<meta charset="utf-8">
<title>Kor'v Meridell Travel – Business Card</title>
<link rel="stylesheet" href="https://fonts.googleapis.com/css2?family=Open+Sans:wght@400;600;700;800&display=swap">
<style>
  :root {
    --stage: #2b2b2d;
    --card: #151516;
    --card-pattern: #1d1d1f;
    --blue: #29abe2;
    --green: #8dc63f;
    --ink: #c9c9cb;
    --muted: #8e8e92;
  }
  * { margin: 0; padding: 0; box-sizing: border-box; }
  html, body {
    width: 1200px; height: 900px; overflow: hidden;
    background: var(--stage);
    font-family: "Open Sans", Arial, sans-serif;
  }
  .stage {
    width: 1200px; height: 900px;
    display: flex; align-items: center; justify-content: center; gap: 40px;
  }
  .card {
    position: relative;
    width: 525px; height: 300px;
    background: var(--card);
    overflow: hidden;
    box-shadow: 0 12px 30px rgba(0,0,0,.45);
  }

  /* Front */
  .holder { position: absolute; left: 34px; top: 44px; }
  .holder-name {
    color: var(--blue); font-weight: 800; font-size: 22px;
    letter-spacing: .5px; text-transform: uppercase; line-height: 1.1;
  }
  .holder-title { color: var(--muted); font-size: 13px; margin-top: 2px; }
  .divider {
    position: absolute; left: 34px; right: 40px; top: 118px;
    height: 1px; background: var(--blue);
  }
  .contact { position: absolute; left: 34px; top: 134px; list-style: none; }
  .contact li {
    display: flex; align-items: center; gap: 8px;
    color: var(--ink); font-size: 13px; line-height: 22px;
  }
  .contact svg { width: 12px; height: 12px; flex: none; }
  .brand {
    position: absolute; right: 34px; top: 42px; text-align: right;
    color: var(--blue); font-weight: 700; font-size: 18px;
    letter-spacing: 1px; text-transform: uppercase; line-height: 1.2;
  }
  .address {
    position: absolute; right: 40px; bottom: 40px; text-align: right;
    color: var(--ink); font-size: 13px; line-height: 20px;
  }
  .base-band {
    position: absolute; left: 0; right: 0; bottom: 0;
    height: 7px; background: var(--blue);
  }

  /* Back */
  .pattern-field {
    position: absolute; inset: 0;
    background: linear-gradient(135deg, var(--card) 0%, var(--card-pattern) 50%, var(--card) 100%);
  }
  .back-brand {
    position: absolute; right: 34px; bottom: 34px;
    color: var(--blue); font-weight: 700; font-size: 16px;
    letter-spacing: 1px; text-transform: uppercase;
  }
</style>
</head>
<body>
<main class="stage">

  <section class="card card-front" aria-label="Card front">
    <div class="holder">
      <p class="holder-name">Dara Velkins</p>
      <p class="holder-title">President</p>
    </div>

    <div class="brand">Kor'v Meridell<br>Travel</div>

    <div class="divider"></div>

    <ul class="contact">
      <li>
        <svg viewBox="0 0 12 12" aria-hidden="true"><path fill="#8dc63f" d="M2.6 1h2l.8 2.4-1.2.9a6 6 0 0 0 2.9 2.9l.9-1.2 2.4.8v2a1 1 0 0 1-1 1A9 9 0 0 1 1.6 2a1 1 0 0 1 1-1z"/></svg>
        555-310-4827
      </li>
      <li>
        <svg viewBox="0 0 12 12" aria-hidden="true"><rect x="1" y="2.5" width="10" height="7" fill="#8dc63f"/><path d="M1 2.5l5 4 5-4" fill="none" stroke="#151516" stroke-width="1"/></svg>
        info@korvmeridell.com
      </li>
      <li>
        <svg viewBox="0 0 12 12" aria-hidden="true"><circle cx="6" cy="6" r="5" fill="none" stroke="#8dc63f" stroke-width="1.2"/><path d="M1 6h10M6 1c-2.5 3-2.5 7 0 10M6 1c2.5 3 2.5 7 0 10" fill="none" stroke="#8dc63f" stroke-width="1"/></svg>
        www.korvmeridell.com
      </li>
    </ul>

    <address class="address" style="font-style:normal">
      1820 Harbor Crest Way<br>Seacliff CA 90000
    </address>

    <div class="base-band"></div>
  </section>

  <section class="card card-back" aria-label="Card back">
    <div class="pattern-field" role="img" aria-label="Tone-on-tone repeating brand watermark pattern"></div>
    <div class="back-brand">Kor'v Meridell Travel</div>
  </section>

</main>
</body>
</html>
```